Brochure Design Project - Glass Cabinets

We are a small but rapidly expanding company providing glass display furniture to retailers and other organisations to display their product. We specialise in all-glass, frameless display cabinets and showcases. Our products include glass cabinets, wall units, shelving units, etc. Our main market was initially householders, then retailers, but has increasingly become corporates who want to display their corporate prizes/trophies, and are also fit-out companies who have discovered our products and are interested in them. We want to make the most of this development, and we want this brochure to help us.
We have identified shop fit-out companies and fit-out designers as a target market for the coming year, so we need some literature that will introduce our company to these businesses, and encourage them to use our products in their designs.
This brochure will not be a product catalogue (we already have that), but a corporate profile that introduces our company and its services. We need to communicate the message that we are a serious provider of good quality glass display furniture, and that we stand for innovation, value, and good design.
We will be giving these brochures out when we make marketing approaches to the shop fit-out companies.
We envisage that the brochure will be a one A4 page brochure, with the back side used for examples of our work. We are open to suggestions about this, however. For example, it could conceivably be DLE format.
We expect some of the copy will be in text boxes. We will upload further details of the examples on page 2 in the next few days.
It needs to be full colour.
It will be offset printed.
The output needs to be PC compatible, preferably produced in Indesign so it is compatible with our software.
Please see our website and other uploaded files for examples of our current imagery. The corporate brochure needn't follow this slavishly, but should be cognizant of it.

Reason: The deadline has been extended because there is some further information I will put up, regarding page two. Also, I will spend some time providing feedback.

Thank you to all who have submitted designs for my project. They are all very much appreciated. I have responded to most of you, but some general comments that come to mind are that the brochure needs to 1) appeal to the emotions more i.e. be more evocative of sophistication. This means not necessarily using just the images I have uploaded, but maybe suggest design elements that are more creative than 'blocky', and 2) be designed to sell the company rather than its products. This is partly my fault, I think, although it is a learning experience for me also. In general I think there is too much information to include, especially copy but also images, forcing designers to make the designs quite boring in order to accommodate it. I intend to cut the information significantly and will repost. Having said that, I am trying to see through the overload of information and look for designs that include elements that are creative and sophisticated. Sometimes less is more. Apologies if I am confusing you, but the main thing is to make the brochure appeal to the emotions i.e. 'this company is sophisticated and and be depended upon', and less to the products themselves. I welcome any questions you may have.

Thanks to all the designers who have submitted designs. There are some great ideas coming through now, and on the basis of these ideas I have been able to determine what the brochure needs to look like much more precisely. Some of the designs have been too crowded, because there has been too much information to include. I have therefore decided that the brochure needs to be a 4 page A4 brochure (A3 folded in half). I have altered the copy in the Word document to reflect this. The middle spread is now dedicated to jobs previously done, and includes logos of other high profile customers. The front page can now be dedicated to providing very basic, introductory information and an eye-catching graphic, while the back page has further detail about the company and contact details. To reflect the fact that this will involve some redesign work, I have increased the budget. I have also extended the deadline by a week. I thank you for your patience, but sometimes a design project is iterative. Please see the newly uploaded files.

Reason: Thanks to all the designers who have submitted designs. There are some great ideas coming through now, and on the basis of these ideas I have been able to determine what the brochure needs to look like much more precisely. Some of the designs have been too crowded, because there has been too much information to include. I have therefore decided that the brochure needs to be a 4 page A4 brochure (A3 folded in half). I have altered the copy in the Word document to reflect this. The middle spread is now dedicated to jobs previously done, and includes logos of other high profile customers. The front page can now be dedicated to providing very basic, introductory information and an eye-catching graphic, while the back page has further detail about the company and contact details. To reflect the fact that this will involve some redesign work, I have increased the budget. I have also extended the deadline by a week. I thank you for your patience, but sometimes a design project is iterative. Please see the newly uploaded files.

Target Market(s)

Shop Fit-out companies, Fit-out designers, Retailers

Industry/Entity Type

Marketing

Requirements
Must have
• Existing logo
Full colour, with overprint

```html
<!DOCTYPE html>
<html lang="en">
<head>
<meta charset="utf-8">
<title>Vitrine House – DL Brochure</title>
<link rel="stylesheet" href="https://fonts.googleapis.com/css2?family=Mukta:wght@500;600;700&family=Open+Sans:wght@400;600&display=swap">
<style>
  :root {
    --backdrop: #e2dfe2;
    --paper: #fbfbf9;
    --ink: #3a2a3c;
    --body-ink: #6d6a6e;
    --leaf: #a8b85a;
    --leaf-light: #dfe6c2;
    --white: #ffffff;
  }
  * { box-sizing: border-box; margin: 0; padding: 0; }
  html, body { width: 1200px; height: 900px; overflow: hidden; }
  body {
    background: var(--backdrop);
    font-family: "Mukta", "Open Sans", sans-serif;
    color: var(--ink);
  }
  .spread {
    position: absolute;
    left: 170px; top: 180px;
    display: flex; gap: 40px;
  }
  .panel {
    position: relative;
    width: 260px; height: 540px;
    background: var(--paper);
    box-shadow: 0 2px 6px rgba(0,0,0,0.18);
    overflow: hidden;
  }
  .panel--cover .panel__content,
  .panel--feature .panel__content {
    position: absolute; left: 0; top: 0;
    width: 214px; height: 100%;
    text-align: center;
  }
  .value-strip {
    position: absolute; right: 0; top: 0;
    width: 46px; height: 100%;
    background: var(--leaf);
    display: flex; flex-direction: column-reverse;
    justify-content: space-around; align-items: center;
    padding: 40px 0;
  }
  .value-strip__word {
    writing-mode: vertical-rl;
    transform: rotate(180deg);
    font-family: "Open Sans", sans-serif;
    font-weight: 600;
    font-size: 17px;
    letter-spacing: 1.5px;
    color: var(--white);
  }
  .headline {
    font-weight: 600;
    font-size: 22px;
    line-height: 1.15;
    color: var(--ink);
  }
  .panel--cover .headline { margin-top: 66px; padding: 0 20px; }
  .panel--feature .headline { margin-top: 66px; padding: 0 14px; }
  .image-slot { display: block; margin: 0 auto; }
  .image-slot--mascot {
    margin-top: 38px;
    width: 180px; height: 180px;
    background: radial-gradient(circle at 50% 55%, #c8602a 0 38%, #f3ece4 39% 48%, var(--white) 70%);
  }
  .image-slot--cubes {
    margin-top: 36px;
    width: 132px; height: 132px;
    background: linear-gradient(160deg, #eef5f4, #c7dedc 60%, #e9f0ef);
  }
  .brand {
    position: absolute; left: 24px; bottom: 84px;
    width: 166px;
    display: flex; align-items: center; justify-content: center; gap: 7px;
    font-weight: 600; font-size: 17px;
    color: var(--leaf);
  }
  .brand__mark { width: 12px; height: 12px; background: var(--leaf); }
  .cta {
    position: absolute; left: 36px; bottom: 68px;
  }
  .cta__label {
    position: absolute; left: 38px; top: 8px;
    width: 86px;
    font-family: "Open Sans", sans-serif;
    font-weight: 600; font-size: 9px; line-height: 1.3;
    text-align: center; color: var(--white);
  }
  .panel--story { padding: 52px 20px 0 20px; }
  .story__title {
    font-weight: 700; font-size: 27px; line-height: 1; color: var(--ink);
  }
  .story__lede {
    margin-top: 6px;
    font-weight: 600; font-size: 14px; line-height: 1.15; color: var(--ink);
  }
  .story__body {
    margin-top: 18px;
    font-family: "Open Sans", sans-serif;
    font-size: 8.5px; line-height: 1.5; color: var(--body-ink);
    max-width: 170px;
  }
  .story__body p + p { margin-top: 10px; }
  .image-slot--cabinet {
    position: absolute; left: 24px; bottom: 30px;
    width: 66px; height: 218px;
    background: linear-gradient(180deg, #e6f0ee 0%, #c5d9d6 80%, #9a9a9e 92%, #8a8a8e 100%);
  }
</style>
</head>
<body>
  <main class="spread">
    <section class="panel panel--cover">
      <div class="panel__content">
        <h1 class="headline">We have the perfect place to show it off.</h1>
        <div class="image-slot image-slot--mascot" role="img" aria-label="Photograph of a plush toy fox sitting on a white background"></div>
        <div class="brand"><span class="brand__mark"></span>Vitrine House</div>
      </div>
      <div class="value-strip">
        <span class="value-strip__word">UNIQUE</span>
        <span class="value-strip__word">INNOVATIVE</span>
        <span class="value-strip__word">CREATIVE</span>
      </div>
    </section>

    <section class="panel panel--story">
      <h2 class="story__title">Glass is timeless,</h2>
      <p class="story__lede">Whatever your situation, a quality cabinet from Vitrine House will suit.</p>
      <div class="story__body">
        <p>Vitrine House is one of the leading suppliers of high quality showcases, display cases and display cabinets.</p>
        <p>We specialise in all-glass display cabinets that minimise visual distraction to the cabinet's contents.</p>
        <p>Our range is unique, our service is exceptional, our attention to detail will surprise you.</p>
      </div>
      <div class="image-slot image-slot--cabinet" role="img" aria-label="Photograph of a tall frameless glass display cabinet with glass shelves"></div>
    </section>

    <section class="panel panel--feature">
      <div class="panel__content">
        <h2 class="headline">Presenting our good quality all-glass frameless displays.</h2>
        <div class="image-slot image-slot--cubes" role="img" aria-label="Photograph of stacked glass cube displays holding small plush toys"></div>
        <div class="cta">
          <svg width="130" height="40" viewBox="0 0 130 40" aria-hidden="true">
            <path d="M2 20 L24 8 L24 2 L110 2 A18 18 0 0 1 110 38 L24 38 L24 32 Z" fill="var(--leaf)"/>
          </svg>
          <p class="cta__label">Why glass?<br>Find out why.</p>
        </div>
      </div>
      <div class="value-strip">
        <span class="value-strip__word">UNIQUE</span>
        <span class="value-strip__word">INNOVATIVE</span>
        <span class="value-strip__word">CREATIVE</span>
      </div>
    </section>
  </main>
</body>
</html>
```